Podcast Art for Bright Belly Radio: Rising above Daily Flares

Read carefully Please. Most submittals so far have not read this.

We're looking for stunning, eye-catching, innovative yet simple podcast art for our first Podcast

Background should be solid, one color

Bright Belly Radio: Rising beyond Daily Flares
with Marcus Telford

Use our Brand Guide including logo, colors, and font
https://lnk.example-short.net/BBR2020StyleKit

Some Podcast Covers I like: https://casts.wavelane-audio.net/

Optional: Captain Flush graphic included above and/or my headshot uploaded below

As you can see humor / medutainment is part of the brand. As we are talking serious topic such as a disease many suffer from you can see the humor in the logo and "captain flush" . Here is the monologue for the first episode to give you a deeper feel on the content

https://files.papermoor-docs.net/doc/7qR_Lk2mWz9PdXc4VtBn8JhYs3FaEo6GuKwTn/edit?share=link

Target Market(s)

Those who suffer from gut issues, are diagnosed with inflammatory bowel disease(IBD), Crohn's Disease or Ulcerative Colitis - also their coaches, doctors, practitioners so functional or integrative medicine doctors/coaches, gastroenterologists etc.

Industry/Entity Type

Health And Wellness

Font styles to use
Other font styles liked:
• Primary: Oswald bold. Secondary: Oswald Medium or light

Requirements
Must have
• 3000 x 3000 pixels
Simple and eye-catching
Brand Guide Logo
Brand Guide Font
Brand Guide Colors including accent color(s)
I did not select colors below because I have included our Brand guide. Please use the exact colors there.
Nice to have
• Maybe my headshot and/or the captain flush graphic - if not too busy and still looks good
Should not have
• - Look busy
- Reverse Logo
- Not follow the Brand Guide
- Anything in the background but one solid color from the brief

```html
<!DOCTYPE html>
<html lang="en">
<head>
<meta charset="utf-8">
<title>Bright Belly Radio: Rising beyond Daily Flares</title>
<link rel="stylesheet" href="https://fonts.googleapis.com/css2?family=Oswald:wght@400;500;600;700&display=swap">
<style>
  :root {
    --pink: #d93a84;
    --navy: #253f78;
    --ice: #c9e6f1;
    --yellow: #fbe27a;
    --photo-light: #cfc8bd;
    --photo-dark: #7d7466;
  }
  html, body {
    margin: 0;
    padding: 0;
    width: 1200px;
    height: 1200px;
    overflow: hidden;
    background: var(--navy);
  }
  .cover {
    position: relative;
    width: 1200px;
    height: 1200px;
    background: var(--navy);
    font-family: "Oswald", sans-serif;
    overflow: hidden;
  }
  .side-band {
    position: absolute;
    left: 0;
    top: 0;
    width: 424px;
    height: 1200px;
    background: var(--pink);
  }
  .divider {
    position: absolute;
    left: 424px;
    top: 0;
    width: 13px;
    height: 1200px;
    background: var(--yellow);
  }
  .brand-name {
    position: absolute;
    left: 0;
    top: 190px;
    width: 424px;
    margin: 0;
    text-align: center;
    color: var(--ice);
    font-weight: 700;
    font-size: 128px;
    line-height: 1.12;
    text-transform: uppercase;
  }
  .show-title {
    position: absolute;
    left: 500px;
    top: 96px;
    margin: 0;
    color: var(--ice);
    font-weight: 600;
    text-transform: uppercase;
  }
  .show-title .line {
    display: block;
    font-size: 186px;
    line-height: 0.98;
  }
  .show-title .joiner {
    display: block;
    font-size: 80px;
    line-height: 1.05;
    text-transform: none;
    padding-left: 10px;
    margin: 8px 0 10px;
  }
  .host {
    position: absolute;
    left: 512px;
    top: 914px;
    margin: 0;
    color: var(--yellow);
    font-weight: 500;
    text-transform: uppercase;
  }
  .host .lead {
    display: block;
    font-size: 30px;
    line-height: 1.2;
    letter-spacing: 1px;
  }
  .host .first {
    display: block;
    font-size: 64px;
    line-height: 1.05;
    letter-spacing: 4px;
  }
  .host .last {
    display: block;
    font-size: 44px;
    line-height: 1.1;
    letter-spacing: 3px;
  }
  .headshot {
    position: absolute;
    left: 840px;
    top: 782px;
    width: 290px;
    height: 290px;
    box-sizing: border-box;
    border: 7px solid var(--pink);
    background: linear-gradient(160deg, var(--photo-light), var(--photo-dark));
  }
</style>
</head>
<body>
  <main class="cover">
    <div class="side-band"></div>
    <div class="divider"></div>

    <p class="brand-name">Bright<br>Belly<br>Radio</p>

    <h1 class="show-title">
      <span class="line">Rising</span>
      <span class="joiner">Beyond</span>
      <span class="line">Daily</span>
      <span class="line">Flares</span>
    </h1>

    <p class="host">
      <span class="lead">With</span>
      <span class="first">Marcus</span>
      <span class="last">Telford</span>
    </p>

    <div class="headshot" role="img" aria-label="Headshot of host Marcus Telford"></div>
  </main>
</body>
</html>
```